Business Card Design needed for start up company Halvora

In need of a new business card designed for a start up company based in Sydney, Halvora is a new start up innovative Company, our mission it to make property accessible for everyday Australian and to become the leading Real Estate platform in Australia. We want it to be fresh and clean.

Industry/Entity Type

Financial

Contact Information for Business Card

Section for Name
Section for Title

HALVORA - The Strength of Pooling
Mobile:
Direct:

Font styles to use
Sans Serif

Colors
33a6d7
0692cd
0255a3
ffffff

Requirements
Must have
• Logo, all business card details

```html
<!DOCTYPE html>
<html lang="en">
<head>
<meta charset="utf-8">
<title>Halvora Business Card</title>
<link href="https://fonts.googleapis.com/css2?family=Jost:wght@400;500;600;700&display=swap" rel="stylesheet">
<style>
  :root {
    --navy: #1f4075;
    --sky: #2a9bd8;
    --sky-bright: #33a6d7;
    --ink: #4a4a4a;
    --paper: #f4f4f4;
    --white: #ffffff;
    --backdrop: #e6e8eb;
    --rule: #b9b9b9;
  }
  * { margin: 0; padding: 0; box-sizing: border-box; }
  html, body {
    width: 1200px; height: 960px; overflow: hidden;
    background: var(--backdrop);
    font-family: "Jost", sans-serif;
  }
  .canvas { position: relative; width: 1200px; height: 960px; }

  .card {
    position: absolute;
    width: 600px; height: 342px;
    border-radius: 18px;
    overflow: hidden;
  }
  .card--front { left: 217px; top: 132px; background: var(--paper); }
  .card--back { left: 382px; top: 505px; background: var(--navy); }

  .brand { position: absolute; display: flex; align-items: center; }
  .brand__dot { border-radius: 50%; background: var(--sky); flex: none; }
  .brand__name { font-weight: 700; line-height: 1; white-space: nowrap; }

  .card--front .brand { left: 68px; top: 132px; width: 240px; }
  .card--front .brand__dot { width: 62px; height: 62px; margin-right: 9px; }
  .card--front .brand__name { font-size: 31px; color: var(--navy); }

  .card--back .brand { left: 0; right: 0; top: 117px; justify-content: center; }
  .card--back .brand__dot { width: 106px; height: 106px; margin-right: 14px; }
  .card--back .brand__name { font-size: 50px; color: var(--white); }

  .divider {
    position: absolute; left: 326px; top: 72px;
    width: 1px; height: 182px; background: var(--rule);
  }

  .contact { position: absolute; left: 355px; top: 70px; color: var(--ink); }
  .contact__name { font-size: 21px; font-weight: 700; color: var(--navy); letter-spacing: 0.3px; line-height: 26px; }
  .contact__title { font-size: 15px; color: var(--sky); line-height: 20px; margin-bottom: 8px; }
  .contact__address { font-size: 14px; line-height: 18px; margin-bottom: 7px; }
  .contact__list { list-style: none; font-size: 14px; line-height: 19.5px; }
  .contact__list li { display: flex; align-items: center; }
  .contact__list svg { width: 12px; height: 12px; margin-right: 9px; fill: var(--navy); flex: none; }

  .footer-band { position: absolute; left: 0; bottom: 0; width: 600px; height: 52px; }
  .tagline {
    position: absolute; left: 0; right: 0; bottom: 9px;
    text-align: center; font-size: 15px; font-weight: 500; color: var(--white);
  }
</style>
</head>
<body>
<main class="canvas">

  <section class="card card--front" aria-label="Business card front">
    <div class="brand">
      <span class="brand__dot"></span>
      <span class="brand__name">HALVORA</span>
    </div>

    <div class="divider"></div>

    <div class="contact">
      <p class="contact__name">MAYA ELLISON</p>
      <p class="contact__title">CEO/FOUNDER</p>
      <p class="contact__address">42 Harbour Crest Road<br>Sydney, NSW 2000</p>
      <ul class="contact__list">
        <li><svg viewBox="0 0 24 24"><path d="M6.6 10.8a15.1 15.1 0 0 0 6.6 6.6l2.2-2.2c.3-.3.7-.4 1-.2 1.1.4 2.3.6 3.6.6.6 0 1 .4 1 1V20c0 .6-.4 1-1 1A17 17 0 0 1 3 4c0-.6.4-1 1-1h3.5c.6 0 1 .4 1 1 0 1.3.2 2.5.6 3.6.1.3 0 .7-.2 1z"/></svg>02 5550 1847</li>
        <li><svg viewBox="0 0 24 24"><path d="M7 1h10a2 2 0 0 1 2 2v18a2 2 0 0 1-2 2H7a2 2 0 0 1-2-2V3a2 2 0 0 1 2-2zm0 3v14h10V4zm5 15.5a1 1 0 1 0 0 2 1 1 0 0 0 0-2z"/></svg>0491 570 326</li>
        <li><svg viewBox="0 0 24 24"><path d="M2 5h20v14H2zm2 2v.5l8 5 8-5V7zm0 2.8V17h16V9.8l-8 5z"/></svg>maya@halvora.com</li>
        <li><svg viewBox="0 0 24 24"><path d="M12 2a10 10 0 1 0 0 20 10 10 0 0 0 0-20zm-1 17.9A8 8 0 0 1 4.2 10L9 14.8v1a2 2 0 0 0 2 2zm6.9-2.5a2 2 0 0 0-1.9-1.4h-1v-3a1 1 0 0 0-1-1H8v-2h2a1 1 0 0 0 1-1V7h2a2 2 0 0 0 2-2v-.4a8 8 0 0 1 2.9 12.8z"/></svg>www.halvora.com</li>
      </ul>
    </div>

    <svg class="footer-band" viewBox="0 0 600 52" preserveAspectRatio="none" aria-hidden="true">
      <path d="M0 28 Q300 -6 600 24 L600 52 L0 52 Z" fill="var(--sky-bright)"/>
      <path d="M0 33 Q300 0 600 29 L600 52 L0 52 Z" fill="var(--navy)"/>
    </svg>
    <p class="tagline">The Strength of Pooling</p>
  </section>

  <section class="card card--back" aria-label="Business card back">
    <div class="brand">
      <span class="brand__dot"></span>
      <span class="brand__name">HALVORA</span>
    </div>
  </section>

</main>
</body>
</html>
```